Veluxa Bone & Motion Business Card

Need a business card using the logo provided. I want brand side of the card to be grey with the logo in the center of the card in white.

On the other side I leave to the designers

Target Market(s)

Personal Injury Attorneys

Industry/Entity Type

Medical

Contact Information for Business Card

Name, CEO. Cell Phone, (Crestbrook, Address, Phone) (Fernhollow, Address, Phone) (Pinegate, Address, Phone)

Colors

Designer to choose only greyscale colors for use in the design.

Requirements
Must have
• Logo by itself on one side

```html
<!DOCTYPE html>
<html lang="en">
<head>
<meta charset="utf-8">
<title>Veluxa Bone &amp; Motion – Business Card</title>
<link rel="stylesheet" href="https://fonts.googleapis.com/css2?family=Lato:wght@700&family=Open+Sans:wght@400;700&display=swap">
<style>
  :root {
    --backdrop: #cbcbcb;
    --card: #a4a6a8;
    --accent: #3a3b3d;
    --light: #ffffff;
    --logo-font: "Lato", sans-serif;
    --text-font: "Open Sans", sans-serif;
  }
  * { box-sizing: border-box; margin: 0; padding: 0; }
  html, body {
    width: 1200px; height: 1200px; overflow: hidden;
    background: var(--backdrop);
  }
  .card {
    position: absolute;
    left: 229px;
    width: 745px;
    height: 418px;
    background: var(--card);
  }
  .card--info { top: 164px; }
  .card--brand { top: 620px; }

  .wordmark {
    position: absolute;
    font-family: var(--logo-font);
    font-weight: 700;
    text-align: center;
    line-height: 1;
    white-space: nowrap;
    transform: translateX(-50%);
  }
  .wordmark__main, .wordmark__sub { display: block; }

  .card--info .wordmark { left: 215px; top: 164px; color: var(--accent); }
  .card--info .wordmark__main { font-size: 58px; letter-spacing: 13px; margin-right: -13px; }
  .card--info .wordmark__sub { font-size: 25px; letter-spacing: 7px; margin-right: -7px; margin-top: 8px; color: var(--light); }

  .card--brand .wordmark { left: 372px; top: 128px; color: var(--light); }
  .card--brand .wordmark__main { font-size: 100px; letter-spacing: 20px; margin-right: -20px; }
  .card--brand .wordmark__sub { font-size: 48px; letter-spacing: 13px; margin-right: -13px; margin-top: 14px; }

  .divider {
    position: absolute;
    left: 394px; top: 52px;
    width: 1.5px; height: 314px;
    background: var(--accent);
  }
  .contact {
    position: absolute;
    left: 419px; top: 44px;
    width: 310px;
    font-family: var(--text-font);
    color: var(--light);
  }
  .contact__name {
    font-weight: 700;
    font-size: 28px;
    color: var(--accent);
    letter-spacing: 0.2px;
    line-height: 1.2;
  }
  .contact__role { font-size: 16px; line-height: 22px; }
  .contact__cell { margin-top: 10px; font-size: 15px; line-height: 22px; }
  .offices { margin-top: 12px; display: grid; gap: 10px; }
  .office { font-size: 13.5px; line-height: 20px; letter-spacing: 0.2px; }
  .office__city {
    font-weight: 700;
    color: var(--accent);
    letter-spacing: 1px;
    margin-right: 8px;
  }
  .phone { display: flex; align-items: center; gap: 4px; }
  .phone svg { width: 16px; height: 16px; fill: none; stroke: var(--accent); stroke-width: 1.8; flex: none; }
</style>
</head>
<body>
  <section class="card card--info">
    <div class="wordmark">
      <span class="wordmark__main">VELUXA</span>
      <span class="wordmark__sub">BONE &amp; MOTION</span>
    </div>
    <div class="divider"></div>
    <div class="contact">
      <h1 class="contact__name">DANIEL KORVATH</h1>
      <p class="contact__role">CEO</p>
      <p class="contact__cell phone">
        <svg viewBox="0 0 18 18" aria-hidden="true"><rect x="5" y="1.5" width="8" height="15" rx="1.2"/><line x1="8" y1="14" x2="10" y2="14"/></svg>
        +123-555-0148
      </p>
      <div class="offices">
        <div class="office">
          <p class="phone"><span class="office__city">CRESTBROOK</span>
            <svg viewBox="0 0 18 18" aria-hidden="true"><path d="M4 2.5l3 3-1.6 2a9 9 0 0 0 5 5l2-1.6 3 3-2 2C8 15.5 2.5 10 2.2 4.5z" fill="var(--accent)" stroke="none"/></svg>
            +123-555-0193</p>
          <p>4127 Marlow Avenue #212, FL 33012</p>
        </div>
        <div class="office">
          <p class="phone"><span class="office__city">FERNHOLLOW</span>
            <svg viewBox="0 0 18 18" aria-hidden="true"><path d="M4 2.5l3 3-1.6 2a9 9 0 0 0 5 5l2-1.6 3 3-2 2C8 15.5 2.5 10 2.2 4.5z" fill="var(--accent)" stroke="none"/></svg>
            +123-555-0227</p>
          <p>860 Tillman Road, Suite 4, FL 33030</p>
        </div>
        <div class="office">
          <p class="phone"><span class="office__city">PINEGATE</span>
            <svg viewBox="0 0 18 18" aria-hidden="true"><path d="M4 2.5l3 3-1.6 2a9 9 0 0 0 5 5l2-1.6 3 3-2 2C8 15.5 2.5 10 2.2 4.5z" fill="var(--accent)" stroke="none"/></svg>
            +123-555-0264</p>
          <p>215 Osgood Street #9, FL 32301</p>
        </div>
      </div>
    </div>
  </section>

  <section class="card card--brand">
    <div class="wordmark">
      <span class="wordmark__main">VELUXA</span>
      <span class="wordmark__sub">BONE &amp; MOTION</span>
    </div>
  </section>
</body>
</html>
```